Roofing web site brvt roofing

Look at some of our competitors web page we like something similar with NYC roofing
https://www.quillbarroofing.example/
Maybe a skyline picture of nyc at the home page with a picture of flat roofing installation

Target Market(s)

Commercial and residential flat roofs

Industry/Entity Type

Flat Roofing industry

Coding

Coded - Design and coding required

Number of Pages Required

2 page

Font styles to use
Decorative
Script

Colors

Designer to choose colors to be used in the design.

Requirements
Must have
• At BRVT Roofing, we are a trusted and reputable roofing company specializing in new construction flat roof installation and repair. With years of experience in the industry, we take pride in providing exceptional roofing solutions to our valued clients. Our team of highly skilled and dedicated roofing professionals understands the unique challenges and requirements of new construction projects. We work closely with builders, contractors, and architects to design and install flat roofs that meet the specific needs of each project. From commercial buildings to residential complexes, we have the expertise to deliver reliable and durable roofing solutions. When it comes to flat roof repairs, we are your go-to experts. Our experienced technicians conduct thorough inspections to identify the root cause of any issues your roof may be experiencing. We utilize the latest industry techniques and high-quality materials to efficiently repair your flat roof, ensuring its integrity and longevity. At BRVT Roofing, we prioritize customer satisfaction above all else. We believe in building strong relationships with our clients by providing exceptional craftsmanship and outstanding customer service. Our team is dedicated to delivering projects on time, within budget, and to the highest standards of quality. We understand that a well-maintained roof is essential for protecting your property and ensuring the safety of its occupants. That's why we use only the best materials and employ skilled professionals who are trained in the latest roofing practices. Our commitment to excellence is evident in every project we undertake. As a fully licensed and insured roofing company, we prioritize safety and adhere to industry regulations and best practices. We take every precaution to create a safe working environment for our team and minimize any disruptions to your daily routine. When you choose BRVT Roofing, you can trust that you are working with a reliable and reputable company that will deliver exceptional results. We are committed to exceeding your expectations and providing you with a roof that is built to last. Contact us today for all your new construction flat roof installation and repair needs.
Nice to have
• NYC skyline background with commercial roofing pictures of torching roofing

```html
<!DOCTYPE html>
<html lang="en">
<head>
<meta charset="utf-8">
<title>BRVT Roofing — Flat Roof Specialists</title>
<link href="https://fonts.googleapis.com/css2?family=Lato:ital,wght@0,400;0,700;0,900;1,400&family=Oswald:wght@400;500;700&display=swap" rel="stylesheet">
<style>
:root{
  --orange:#f26a2e;
  --orange-dark:#e35a1f;
  --ink:#1a1a1a;
  --text:#3a3a3a;
  --muted:#8a8a8a;
  --line:#d9d9d9;
  --light:#f0f0f0;
  --dark:#000;
  --white:#fff;
}
*{box-sizing:border-box;margin:0;padding:0}
html,body{width:1200px;height:5034px;overflow:hidden}
body{font-family:"Lato",sans-serif;color:var(--text);background:var(--white);position:relative}
.wrap{width:918px;margin:0 auto;position:relative}
.btn{display:inline-block;background:var(--orange);color:var(--white);font-size:12px;padding:9px 20px;text-decoration:none;border:1px solid var(--orange)}
.btn.ghost{background:var(--white);color:var(--orange)}
h2.title{font-family:"Lato",sans-serif;font-weight:700;font-size:30px;color:var(--ink);text-align:center}
.photo{display:block}

/* header */
.site-header{height:88px;display:flex;align-items:center;justify-content:space-between;padding:0 141px}
.brand{font-family:"Oswald",sans-serif;font-weight:400;font-size:26px;color:var(--ink);line-height:1}
.nav{display:flex;align-items:center;gap:38px;font-size:12px}
.nav a{color:var(--ink);text-decoration:none}
.nav .btn{color:var(--white);padding:10px 22px}

/* hero */
.hero{height:580px;position:relative;background:linear-gradient(180deg,#5b8fc9 0%,#8fb7de 22%,#2b2b2d 36%,#1f1f21 55%,#b67a46 62%,#c98d55 100%);text-align:center;padding-top:46px}
.hero h1{font-family:"Oswald",sans-serif;font-weight:700;font-size:60px;color:var(--ink);letter-spacing:1px;line-height:1}
.hero p{font-size:14px;font-weight:700;color:var(--ink);width:600px;margin:16px auto 12px;line-height:1.45}

/* services */
.services{height:575px;padding-top:110px}
.service-row{display:flex;justify-content:center;gap:24px;margin-top:26px;position:relative}
.card{width:290px;height:262px;background:var(--white);box-shadow:0 2px 10px rgba(0,0,0,.12);padding:30px 24px}
.card.active{background:var(--orange);color:var(--white)}
.card h3{font-size:16px;font-weight:700;color:var(--ink);margin:22px 0 14px;padding-bottom:18px;border-bottom:1px solid var(--line)}
.card.active h3{color:var(--white);border-color:rgba(255,255,255,.7)}
.card p{font-size:12px;line-height:1.8}
.card svg{width:62px;height:58px}
.arrow{position:absolute;top:110px;width:44px;height:44px;border-radius:50%;display:flex;align-items:center;justify-content:center}
.arrow.prev{left:-66px;border:2px solid var(--ink)}
.arrow.next{right:-66px;background:var(--orange)}
.services .center{text-align:center;margin-top:28px}

/* about */
.about{height:570px;background:var(--light);padding-top:84px}
.about .wrap{display:flex;gap:90px}
.about-media{position:relative;width:425px;height:388px}
.about-media .frame{position:absolute;left:14px;top:14px;width:425px;height:390px;border:1px solid var(--orange)}
.about-media .photo{position:relative;width:425px;height:388px;background:linear-gradient(135deg,#a9a9a5,#6d6f72 55%,#3d3f45)}
.about-copy{width:405px}
.about-copy h2{font-size:30px;font-weight:700;color:var(--ink);line-height:1.2;margin-bottom:14px}
.about-copy p{font-size:11.5px;line-height:1.9;margin-bottom:8px;color:var(--ink)}
.about-copy .btn{margin-top:14px}

/* projects */
.projects{height:984px;position:relative;padding-top:80px}
.projects .band{position:absolute;left:0;top:0;width:1200px;height:460px;background:linear-gradient(160deg,#3a3b40,#17181b 70%)}
.projects .wrap{z-index:1}
.projects h2{font-size:30px;font-weight:700;color:var(--white)}
.projects .intro{font-size:11.5px;line-height:1.9;color:var(--white);margin:10px 0 24px}
.grid4{display:grid;grid-template-columns:repeat(4,219px);gap:15px}
.grid2{display:grid;grid-template-columns:repeat(2,452px);gap:15px;margin-top:22px}
.grid4 .photo,.grid2 .photo{height:317px}
.p1{background:linear-gradient(160deg,#b9b6ad,#3f3e3b)}
.p2{background:linear-gradient(160deg,#d0673c,#9c4a2c)}
.p3{background:linear-gradient(180deg,#3c6fb1,#7a9cc4 70%,#d9d9d9)}
.p4{background:linear-gradient(160deg,#e6ecef,#aab6bd)}
.p5{background:linear-gradient(150deg,#cfcac2,#b33a3a 45%,#6f6f6f)}
.p6{background:linear-gradient(180deg,#6f9fd6 0%,#9ec0e3 30%,#262628 45%,#c48b52 60%,#b67a46 100%)}
.projects .center{text-align:center;margin-top:30px}

/* reviews */
.reviews{height:560px;padding-top:50px}
.review{display:flex;justify-content:space-between;align-items:center;margin-top:30px}
.review-copy{width:455px;position:relative}
.review-copy h3{font-size:27px;font-weight:700;color:var(--ink);margin-bottom:14px}
.review-copy blockquote{font-style:italic;font-size:15.5px;line-height:1.85;color:var(--ink)}
.review-copy cite{display:block;font-style:normal;font-size:15px;margin-top:32px;color:var(--ink)}
.dots{display:flex;gap:6px;margin-top:12px}
.dots i{width:8px;height:8px;border-radius:50%;background:#c9c9c9}
.dots i:first-child{background:var(--orange)}
.quote-mark{position:absolute;right:70px;bottom:60px}
.avatar{position:relative;width:390px;height:370px}
.avatar .ring{position:absolute;left:0;top:0;width:390px;height:370px;border-radius:50%;border:2px solid #e6e6e6}
.avatar .portrait{position:absolute;left:28px;top:22px;width:330px;height:330px;border-radius:50%;background:radial-gradient(circle at 50% 40%,#d7b59c,#8aa7c2 70%)}
.avatar .badge{position:absolute;left:0;top:178px;width:38px;height:38px;border-radius:50%;background:var(--orange)}
.avatar .thumb{position:absolute;left:12px;bottom:0;width:90px;height:90px;border-radius:50%;border:4px solid var(--white);background:linear-gradient(150deg,#9dbbe0,#6a6a6a)}

/* why */
.why{height:405px;background:var(--light);padding-top:70px;text-align:center}
.features{display:flex;justify-content:space-between;margin-top:20px}
.feature{width:153px;border-right:1px solid var(--line);font-size:11.5px;color:var(--ink);line-height:1.35}
.feature:last-child{border:0}
.feature .ico{width:86px;height:86px;border-radius:50%;margin:0 auto 12px;display:flex;align-items:center;justify-content:center;border:3px solid var(--white);box-shadow:0 0 0 1px var(--line)}
.ico.o{background:var(--orange)}
.ico.k{background:var(--ink)}
.why .btn{margin-top:22px}

/* banner */
.banner{height:279px;background:linear-gradient(180deg,#f47a3e,#ec5f25);text-align:center;padding-top:80px;color:var(--white)}
.banner .kicker{font-size:30px;font-weight:400}
.banner h2{font-size:40px;font-weight:700;margin:8px 0 14px}

/* contact */
.contact{height:532px;padding-top:80px}
.form{width:578px;margin:36px auto 0;display:grid;grid-template-columns:1fr 1fr;column-gap:26px;row-gap:30px}
.field{border-bottom:1px solid #cfcfcf;position:relative;padding-bottom:12px}
.field label{display:block;font-size:9.5px;color:var(--muted);margin-bottom:10px}
.field span{font-size:10.5px;color:var(--ink)}
.field svg{position:absolute;right:4px;bottom:12px}
.field.wide{grid-column:1/3;height:88px}
.contact .center{text-align:center;margin-top:32px}
.contact .btn{padding:10px 26px}

/* footer */
.site-footer{height:332px;background:var(--dark);color:var(--white);padding-top:44px}
.site-footer .wrap{display:flex}
.site-footer h4{font-size:15px;font-weight:700;margin-bottom:22px}
.col-links{width:181px}
.col-links li{list-style:none;font-size:11px;margin-bottom:19px}
.col-links li::before{content:"›";margin-right:12px}
.col-contact{width:305px}
.row{display:flex;gap:12px;margin-bottom:20px;font-size:11.5px;line-height:1.6}
.row b{display:block;font-size:13px}
.circ{width:26px;height:26px;border:1px solid var(--white);border-radius:50%;flex:none;display:flex;align-items:center;justify-content:center}
.col-social{width:223px}
.col-social .row{align-items:center;margin-bottom:22px}
.col-brand{padding-top:50px}
.col-brand .brand{color:var(--white);font-size:30px}
.accredit{width:140px;height:52px;border-radius:6px;background:#1f5e8a;border:2px solid var(--white);margin:20px 0 0 34px}
.copyright{height:52px;background:var(--orange);color:var(--white);text-align:center;font-size:11.5px;line-height:52px}
</style>
</head>
<body>

<header class="site-header">
  <div class="brand">BRVT Roofing</div>
  <nav class="nav"><a href="#">Home</a><a href="#">About Us</a><a class="btn" href="#">Contact Us</a></nav>
</header>

<section class="hero" role="img" aria-label="Photo of a dark shingle roof with a dormer window over warm timber cladding against a blue sky">
  <h1>FLAT ROOF SPECIALISTS</h1>
  <p>Flat Roof Installation, Repair &amp; Restoration Specialists For: Commercial, Real Estate Management, Business, Schools, Warehouses</p>
  <a class="btn" href="#">Contact Us</a>
</section>

<section class="services">
  <h2 class="title">Our Services</h2>
  <div class="wrap">
    <div class="service-row">
      <div class="arrow prev"><svg width="20" height="20" viewBox="0 0 20 20"><path d="M16 10H4M9 5l-5 5 5 5" fill="none" stroke="#1a1a1a" stroke-width="2"/></svg></div>
      <article class="card active">
        <svg viewBox="0 0 62 58" fill="none" stroke="#fff" stroke-width="2"><path d="M4 50l22-22 22 22M12 42h28M18 36h16"/><circle cx="42" cy="14" r="9"/><path d="M42 8v6l4 3"/></svg>
        <h3>Roof Leak Repairs</h3>
        <p>Flat roofing maintenance includes draining water, repairing your roof's infiltration system, and getting rid of debris.</p>
      </article>
      <article class="card">
        <svg viewBox="0 0 62 58" fill="none" stroke="#1a1a1a" stroke-width="2"><path d="M4 50l10-38h34l10 38zM19 12l-5 38M29 12v38M39 12l4 38M8 34h46M11 22h40"/></svg>
        <h3>Flashing Services</h3>
        <p>Roof flashing plays an important role in leak prevention at the most vulnerable areas of your roof.</p>
      </article>
      <article class="card">
        <svg viewBox="0 0 62 58" fill="none" stroke="#1a1a1a" stroke-width="2"><path d="M8 20a14 14 0 0128 0zM6 20h32M12 26v8a10 10 0 0020 0v-8M4 56a18 12 0 0136 0"/><path d="M50 34c-5 7-7 10-7 13a7 7 0 0014 0c0-3-2-6-7-13z"/></svg>
        <h3>Waterproofing Experts</h3>
        <p>Our highly-skilled technicians will expertly diagnose your problem areas and provide you solution to your specific need.</p>
      </article>
      <div class="arrow next"><svg width="20" height="20" viewBox="0 0 20 20"><path d="M4 10h12M11 5l5 5-5 5" fill="none" stroke="#fff" stroke-width="2"/></svg></div>
    </div>
    <div class="center"><a class="btn" href="#">Contact Us</a></div>
  </div>
</section>

<section class="about">
  <div class="wrap">
    <div class="about-media">
      <div class="frame"></div>
      <div class="photo" role="img" aria-label="Photo of a roofer in a hard hat kneeling to seal a flat roof membrane"></div>
    </div>
    <div class="about-copy">
      <h2>About BRVT Roofing</h2>
      <p>Marcus brought together the best in the business to create his dream. Though he takes pride in all aspects of roofing, working and living on the coast has lead to a passion for quick, efficient, and transparent repairs to storm damaged homes.</p>
      <p>Lorem ipsum dolor sit amet consectetur adipiscing elit. Vestibulum hendrerit scelerisque elit. Innec risus dictum, convallis nibh id convallis est. Etiam nec lacus sed nisi mattis dictum. Interdum et malesuada fames ac ante ipsum primis in faucibus.</p>
      <p>Lorem ipsum dolor sit amet consectetur adipiscing elit. Vestibulum hendrerit scelerisque elit. Innec risus dictum, convallis nibh id convallis est. Etiam nec lacus sed nisi mattis dictum. Interdum et malesuada fames ac ante ipsum primis in faucibus.</p>
      <a class="btn" href="#">Find Out More</a>
    </div>
  </div>
</section>

<section class="projects">
  <div class="band" role="img" aria-label="Dark photo of roof shingles under a night sky"></div>
  <div class="wrap">
    <h2>Featured Projects</h2>
    <p class="intro">Lorem ipsum dolor sit amet consectetur adipiscing elit. Vestibulum hendrerit scelerisque elit. In nec risus dictum convallis nibh id convallis est. Etiam nec lacus sed nisi mattis dictum. Interdum et malesuada fames ac ante ipsum primis in faucibus. Donec aliquam varius velit nec pharetra. Aenean velit enim dictum convallis tempus, iaculis ac lacus. Ut tristique rhoncus ullamcorper. Suspendisse laoreet varius nisl, at feugiat magna venenatis et.</p>
    <div class="grid4">
      <div class="photo p1" role="img" aria-label="Roofers torching down a flat roof membrane"></div>
      <div class="photo p2" role="img" aria-label="Worker on a terracotta tile roof beside a skylight"></div>
      <div class="photo p3" role="img" aria-label="Roofer working on a roof edge against a blue sky"></div>
      <div class="photo p4" role="img" aria-label="Worker applying white coating to a flat roof"></div>
    </div>
    <div class="grid2">
      <div class="photo p5" role="img" aria-label="Roofer fitting a skylight window"></div>
      <div class="photo p6" role="img" aria-label="Dark shingle roof with dormer window over timber cladding"></div>
    </div>
    <div class="center"><a class="btn" href="#">View All</a></div>
  </div>
</section>

<section class="reviews">
  <h2 class="title">Customer Reviews</h2>
  <div class="wrap">
    <div class="review">
      <div class="review-copy">
        <h3>Lorem Ipsum Dolor Sit Amet</h3>
        <blockquote>Donec ultrices velit eu ligula gravida tempus risus scelerisque. Duis vitae est eget lectus rutrum facilisis in eget enim. Nullam porttitor justo iaculis diam auctor lobortis. Vestibulum porttitor metus eget condimentum vehicula. Suspendisse nec tellus nibh ornare malesuada. Duis orci sit amet lectus soltudin veenatis. Quisque quis purus scelerisque.</blockquote>
        <svg class="quote-mark" width="44" height="36" viewBox="0 0 44 36"><path d="M2 2h16v16l-8 16H4l6-14H2zM24 2h16v16l-8 16h-6l6-14h-8z" fill="#e2e2e2"/></svg>
        <cite>Owen Hartley</cite>
        <div class="dots"><i></i><i></i><i></i><i></i></div>
      </div>
      <div class="avatar">
        <div class="ring"></div>
        <div class="portrait" role="img" aria-label="Portrait photo of a smiling customer"></div>
        <div class="badge"></div>
        <div class="thumb" role="img" aria-label="Small roof photo"></div>
      </div>
    </div>
  </div>
</section>

<section class="why">
  <h2 class="title">Why Chose Us</h2>
  <div class="wrap">
    <div class="features">
      <div class="feature"><div class="ico o"><svg width="36" height="36" viewBox="0 0 36 36" fill="none" stroke="#fff" stroke-width="2"><circle cx="18" cy="14" r="9"/><path d="M12 22l-3 11 9-4 9 4-3-11"/></svg></div>Licensed, Bonded,<br>&amp; Insured</div>
      <div class="feature"><div class="ico k"><svg width="36" height="36" viewBox="0 0 36 36" fill="none" stroke="#fff" stroke-width="2"><rect x="4" y="10" width="28" height="20" rx="2"/><path d="M13 10V6h10v4M4 18h28"/></svg></div>Reliable &amp; Experienced<br>Professionals</div>
      <div class="feature"><div class="ico o"><svg width="36" height="36" viewBox="0 0 36 36" fill="none" stroke="#fff" stroke-width="2"><rect x="8" y="6" width="20" height="26" rx="2"/><path d="M13 14h10M13 20h10M13 26h6"/></svg></div>Free Evaluations<br>&amp; Estimates</div>
      <div class="feature"><div class="ico k"><svg width="36" height="36" viewBox="0 0 36 36" fill="none" stroke="#fff" stroke-width="2"><path d="M18 4l12 5v9c0 8-6 13-12 15-6-2-12-7-12-15V9z"/><path d="M12 18l4 4 8-8"/></svg></div>Lead-Safe Certified</div>
      <div class="feature"><div class="ico o"><svg width="36" height="36" viewBox="0 0 36 36" fill="none" stroke="#fff" stroke-width="2"><circle cx="18" cy="18" r="13"/><path d="M18 10v8l5 4"/></svg></div>24/7 Emergency<br>Response</div>
      <div class="feature"><div class="ico k"><svg width="36" height="36" viewBox="0 0 36 36"><circle cx="18" cy="18" r="10" fill="#fff"/></svg></div>Accredited<br>Business</div>
    </div>
    <a class="btn" href="#">Contact Us</a>
  </div>
</section>

<section class="banner" role="img" aria-label="Orange clay roof tiles background">
  <div class="kicker">See What We've Been Working On...</div>
  <h2>View Some of Our Latest Project</h2>
  <a class="btn ghost" href="#">Contact Us</a>
</section>

<section class="contact">
  <h2 class="title">Quick Contact</h2>
  <div class="form">
    <div class="field"><label>First Name</label><span>Daniel</span><svg width="16" height="16" viewBox="0 0 16 16" fill="none" stroke="#999"><circle cx="8" cy="5" r="3.5"/><path d="M1.5 15a6.5 5 0 0113 0z"/></svg></div>
    <div class="field"><label>Last Name</label><span>Reyes</span><svg width="16" height="16" viewBox="0 0 16 16" fill="none" stroke="#999"><circle cx="8" cy="5" r="3.5"/><path d="M1.5 15a6.5 5 0 0113 0z"/></svg></div>
    <div class="field"><label>Phone</label><span>123 456 7890</span><svg width="16" height="16" viewBox="0 0 16 16" fill="none" stroke="#999"><path d="M3 1.5l3 3-1.5 2a9 9 0 005 5l2-1.5 3 3-2 2C6 14 2 10 1.5 3.5z"/></svg></div>
    <div class="field"><label>Email</label><span>daniel@reyesmail.example</span><svg width="18" height="14" viewBox="0 0 18 14" fill="none" stroke="#999"><rect x="1" y="1" width="16" height="12" rx="1"/><path d="M1 2l8 6 8-6"/></svg></div>
    <div class="field wide"><label>Message</label><span>Type Your Message</span><svg style="top:22px;bottom:auto" width="18" height="16" viewBox="0 0 18 16" fill="none" stroke="#999"><path d="M2 2h10v7H6l-3 3V9H2zM14 5h2v7h-1v2l-2-2H8v-1"/></svg></div>
  </div>
  <div class="center"><a class="btn" href="#">Submit Now</a></div>
</section>

<footer class="site-footer">
  <div class="wrap">
    <div class="col-links">
      <h4>Quick Links</h4>
      <ul><li>Home</li><li>About Us</li><li>Contact Us</li></ul>
    </div>
    <div class="col-contact">
      <h4>Contact Details</h4>
      <div class="row"><span class="circ"><svg width="12" height="14" viewBox="0 0 12 14" fill="none" stroke="#fff"><path d="M6 13s5-5 5-8A5 5 0 001 5c0 3 5 8 5 8z"/><circle cx="6" cy="5" r="1.6"/></svg></span><div><b>Address</b>12 Lorem Imsum, Street Name,<br>City Name, Country - 12345</div></div>
      <div class="row"><span class="circ"><svg width="12" height="12" viewBox="0 0 16 16" fill="none" stroke="#fff" stroke-width="1.5"><path d="M3 1.5l3 3-1.5 2a9 9 0 005 5l2-1.5 3 3-2 2C6 14 2 10 1.5 3.5z"/></svg></span><div><b>Phone</b>555-010-2478</div></div>
      <div class="row"><span class="circ"><svg width="12" height="10" viewBox="0 0 18 14" fill="none" stroke="#fff" stroke-width="1.5"><rect x="1" y="1" width="16" height="12"/><path d="M1 2l8 6 8-6"/></svg></span><div><b>Email</b>info@brvtroofing.com</div></div>
    </div>
    <div class="col-social">
      <h4>Follow Us</h4>
      <div class="row"><span class="circ"></span>Friendspace</div>
      <div class="row"><span class="circ"></span>Chirper</div>
      <div class="row"><span class="circ"></span>ProNetwork</div>
      <div class="row"><span class="circ"></span>VidStream</div>
    </div>
    <div class="col-brand">
      <div class="brand">BRVT Roofing</div>
      <div class="accredit"></div>
    </div>
  </div>
</footer>
<div class="copyright">© 2024 BRVT Roofing - All Rights Reserved.</div>

</body>
</html>
```